Web Design Project - brivolta

I'm building an agency for marketing solutions but also medical education and patients education for pharmaceutical companies, medical societies and patient advocacy groups. We want to be perceived as the most innovative in the market. We work through design thinking solutions for campaigns and services.
I love some websites based on Swiss style design like www.quorlinex.com
We are a small group of designers, physicians and creatives working together to deliver the best experiences in our market.
We decided to also use pixel bazaar expecting that we maybe found a great idea we didn't thought about yet.

I'm extending it for more 2 weeks

Reason: I need the best design you can. Only PSD. No code needed. Love Swiss style, like velmora 5 and quorlinex.com I'm extending the deadline until get something great. Willing to extend as much as needed.

Target Market(s)

Pharmaceutical companies, physicians, medical societies, patients advocacy groups

Industry/Entity Type

Pharmaceutical

Font styles to use
Other font styles liked:
• Helvetia family

Colors

Designer to choose colors to be used in the design.

Requirements
Must have
• Must be innovative like www.quorlinex.com
Nice to have
• Cool menus
Should not have
• Not to appear too much Comercial. We like to be a boutique in this market. Craftsmen working with less clients at time but delivering precious stones.

```html
<!DOCTYPE html>
<html lang="en">
<head>
<meta charset="utf-8">
<title>Brivolta — Marketing Solutions</title>
<link rel="stylesheet" href="https://fonts.googleapis.com/css2?family=Open+Sans:wght@300;400;700;800&display=swap">
<style>
  :root{
    --bg:#18191b;
    --logo:#6d6e70;
    --accent:#dc3a35;
    --nav:#a9aaab;
    --footer-text:#6a6b6d;
    --rule:#2a2b2d;
    --red:#dc3a35;
    --slate:#303a3b;
    --navy:#3c5896;
    --pink:#e6365f;
    --teal:#26aaa2;
    --ocean:#0084b6;
    --orange:#e25d1e;
    --white:#ffffff;
  }
  *{box-sizing:border-box;margin:0;padding:0}
  html,body{width:1172px;height:1200px;overflow:hidden;background:var(--bg);font-family:"Open Sans",Arial,sans-serif;color:var(--white)}
  .site-header{height:174px;position:relative}
  .brand{position:absolute;top:44px;left:0;width:100%;display:flex;justify-content:center;align-items:center;gap:8px}
  .brand-mark{width:12px;height:12px;background:var(--accent)}
  .brand-name{font-weight:800;font-size:33px;letter-spacing:-1.5px;color:var(--logo);text-transform:uppercase;line-height:1}
  .main-nav{position:absolute;top:124px;left:0;width:100%;display:flex;justify-content:center;align-items:center;font-size:10.5px;color:var(--nav);text-transform:uppercase}
  .main-nav a{color:inherit;text-decoration:none}
  .main-nav .sep{margin:0 31px}
  .tile-grid{display:grid;grid-template-columns:repeat(5,234.4px);grid-template-rows:repeat(4,222.6px)}
  .tile{position:relative;border-right:1px solid rgba(255,255,255,.55);border-bottom:1px solid rgba(255,255,255,.55);display:flex;flex-direction:column;justify-content:flex-end;padding:0 0 31px 30px;overflow:hidden}
  .tile h2{font-weight:700;font-size:33px;line-height:1.05;letter-spacing:0;text-transform:uppercase;margin-bottom:6px;white-space:nowrap}
  .tile p{font-weight:300;font-size:18.5px;line-height:23px;text-transform:uppercase}
  .tile.feature{padding:0 0 21px 33px}
  .tile.feature h2{font-size:44px;margin-bottom:8px}
  .tile.feature p{font-size:19px;line-height:27px;font-weight:300}
  .c-red{background:var(--red)}
  .c-slate{background:var(--slate)}
  .c-navy{background:var(--navy)}
  .c-pink{background:var(--pink)}
  .c-teal{background:var(--teal)}
  .c-ocean{background:var(--ocean)}
  .c-orange{background:var(--orange)}
  .photo-thinker{background:linear-gradient(135deg,#d6d6d4,#5a5a5a 70%,#2a2a2a)}
  .photo-portrait{background:radial-gradient(circle at 55% 35%,#bdbdbd,#5c5c5c 45%,#1d1d1d 85%)}
  .photo-smile{background:linear-gradient(180deg,#dce5ee,#a87a5d 50%,#d8e2ee)}
  .photo-nurse{background:linear-gradient(180deg,#f4f4f4,#c9a08b 40%,#5f8fc9 75%)}
  .photo-lookout{background:linear-gradient(180deg,#c7c9c8,#7b8487 45%,#2b2f3e 75%,#8a8175)}
  .photo-stethoscope{background:radial-gradient(circle at 45% 40%,#f1f1f1,#d8cfc8 55%,#a9bfc7)}
  .photo-lab{background:linear-gradient(135deg,#8fc0e6,#d9b27a 45%,#b04a1e 70%,#4e8ccc)}
  .photo-chess{background:linear-gradient(180deg,#d4d4d2,#a8a59f 55%,#3b3027 90%)}
  .span-2x2{grid-column:span 2;grid-row:span 2}
  .span-col2{grid-column:span 2}
  .span-row2{grid-row:span 2}
  .site-footer{position:absolute;top:1113px;left:0;width:1172px;border-top:1px solid var(--rule);height:87px}
  .copyright{position:absolute;left:125px;top:30px;font-size:9.5px;color:var(--footer-text);text-transform:uppercase}
  .social{position:absolute;left:872px;top:32px;display:flex;gap:24px}
  .social span{width:10px;height:10px;border-radius:50%;background:var(--footer-text)}
</style>
</head>
<body>
  <header class="site-header">
    <div class="brand"><span class="brand-mark"></span><span class="brand-name">Brivolta</span></div>
    <nav class="main-nav">
      <a href="#">Home</a><span class="sep">/</span>
      <a href="#">About us</a><span class="sep">/</span>
      <a href="#">Services</a><span class="sep">/</span>
      <a href="#">Blog</a><span class="sep">/</span>
      <a href="#">Contact us</a>
    </nav>
  </header>

  <main class="tile-grid">
    <div class="tile photo-thinker" role="img" aria-label="Businessman in glasses, hand on chin"></div>
    <div class="tile c-red"><h2>Agency</h2><p>For marketing<br>solutions</p></div>
    <div class="tile feature span-2x2 photo-portrait" role="img" aria-label="Black and white portrait of a man in glasses">
      <h2>Marketing</h2><p>Lorem ipsum is simply<br>dummy text</p>
    </div>
    <div class="tile photo-smile" role="img" aria-label="Smiling young woman"></div>
    <div class="tile c-slate"><h2>Dealing</h2><p>For marketing<br>solutions</p></div>
    <div class="tile photo-nurse" role="img" aria-label="Nurse with stethoscope"></div>
    <div class="tile c-navy"><h2>Solutions</h2><p>For marketing<br>solutions</p></div>
    <div class="tile span-row2 photo-lookout" role="img" aria-label="Businessman with binoculars and briefcase by the sea"></div>
    <div class="tile c-pink"><h2>Lorem</h2><p>For marketing<br>solutions</p></div>
    <div class="tile photo-stethoscope" role="img" aria-label="Doctor holding out a stethoscope"></div>
    <div class="tile c-teal"><h2>Ipsum</h2><p>For marketing<br>solutions</p></div>
    <div class="tile photo-lab" role="img" aria-label="Scientist examining a flask"></div>
    <div class="tile c-ocean"><h2>Exchange</h2><p>For marketing<br>solutions</p></div>
    <div class="tile span-col2 photo-chess" role="img" aria-label="Man moving a chess piece"></div>
    <div class="tile c-orange"><h2>Online</h2><p>For marketing<br>solutions</p></div>
  </main>

  <footer class="site-footer">
    <p class="copyright">©2014. Brivolta. All rights reserved.</p>
    <div class="social" aria-label="Social links"><span></span><span></span><span></span><span></span><span></span><span></span></div>
  </footer>
</body>
</html>
```